Corporate Business Card

Very professional, Modern, Not to busy, include phone address email, website
(253) 617-4930, 18761 52nd Avenue S, Kent, WA 98047, martin@plumlinegroup.com, varkoworks.com

Target Market(s)

Manufacturing

Industry/Entity Type

Aero, machining, manufacturing, Off road racing

Contact Information for Business Card

Phone, address email, website

```html
<!DOCTYPE html>
<html lang="en">
<head>
<meta charset="utf-8">
<title>Varko Works — Business Card</title>
<link href="https://fonts.googleapis.com/css2?family=Montserrat:wght@400;700&display=swap" rel="stylesheet">
<style>
  :root {
    --backdrop: #d8d2c2;
    --card: #19191a;
    --brand-blue: #1d3b82;
    --brand-blue-dim: #1a346f;
    --text-light: #f2f2f2;
    --emboss: #2a2a2b;
  }
  * { margin: 0; padding: 0; box-sizing: border-box; }
  html, body {
    width: 1116px; height: 1200px; overflow: hidden;
    background: var(--backdrop);
    font-family: "Montserrat", sans-serif;
  }
  .card {
    position: absolute; left: 224px; width: 668px; height: 384px;
    background: var(--card); border-radius: 28px;
    box-shadow: 0 14px 24px rgba(0,0,0,0.28);
  }
  .card--front { top: 177px; }
  .card--back { top: 639px; }

  .wordmark {
    position: absolute; left: 0; right: 0; text-align: center;
    font-weight: 700; letter-spacing: 2px; color: var(--brand-blue);
  }
  .card--front .wordmark { top: 62px; font-size: 50px; }
  .card--back .wordmark { top: 152px; font-size: 60px; color: var(--emboss); }

  .person { position: absolute; left: 0; right: 0; top: 198px; text-align: center; }
  .person__name { font-size: 24px; font-weight: 700; color: var(--brand-blue); letter-spacing: 0.5px; line-height: 28px; }
  .person__role { font-size: 16px; color: var(--text-light); margin-top: 2px; }

  .address {
    position: absolute; right: 356px; top: 288px; text-align: right;
    font-size: 16px; line-height: 26px; color: var(--text-light);
  }
  .divider {
    position: absolute; left: 335px; top: 279px; width: 2px; height: 68px;
    background: var(--brand-blue-dim);
  }
  .contacts {
    position: absolute; left: 357px; top: 275px; list-style: none;
    font-size: 16px; line-height: 25.5px; color: var(--text-light);
  }
  .contacts li { display: flex; align-items: center; gap: 4px; }
  .contacts svg { width: 13px; height: 13px; flex: none; }
</style>
</head>
<body>
  <section class="card card--front">
    <div class="wordmark">VARKO WORKS</div>
    <div class="person">
      <div class="person__name">DANIEL REYES</div>
      <div class="person__role">Owner/CEO</div>
    </div>
    <div class="address">4170, 18761 52nd Avenue<br>S, Kent, WA 98047</div>
    <div class="divider"></div>
    <ul class="contacts">
      <li>
        <svg viewBox="0 0 16 16" aria-hidden="true"><path fill="#1d3b82" d="M3.5 1.5l2.5 3-1.5 1.8c.9 1.9 2.3 3.3 4.2 4.2l1.8-1.5 3 2.5-1.6 2.5C6.5 13.5 2.5 9.5 1 3.1z"/></svg>
        (253) 617-4930
      </li>
      <li>
        <svg viewBox="0 0 16 16" aria-hidden="true"><rect x="1" y="3.5" width="14" height="9" fill="#1d3b82"/><path d="M1.5 4l6.5 5 6.5-5" fill="none" stroke="#19191a" stroke-width="1.2"/></svg>
        martin@plumlinegroup.com
      </li>
      <li>
        <svg viewBox="0 0 16 16" aria-hidden="true"><circle cx="8" cy="8" r="6.5" fill="#1d3b82"/><path d="M1.5 8h13M8 1.5c-2.5 3-2.5 10 0 13M8 1.5c2.5 3 2.5 10 0 13" fill="none" stroke="#19191a" stroke-width="1"/></svg>
        www.varkoworks.com
      </li>
    </ul>
  </section>

  <section class="card card--back">
    <div class="wordmark">VARKO WORKS</div>
  </section>
</body>
</html>
```